Corvane Business Cards

Front of business card will have logo, name, address, & telephone number. Back of card will have a list of services provided - Roads, Substation Pads, Temporary Pads, Site Pads, Land Leveling, Powerline Row Cleaning, Land Clearing, Gates, Fencing, Construction Entrances, Excavation, Trenching, Underground Utilities, Directional Boring, Pile Driving. We are a construction company that uses heavy equipment like bulldozers, motor graders/blades, dump trucks, backhoes, hydro axes, & skid loaders. We build roads, pads, & install electric utility lines & waterlines underground. This logo is new. The word "Construction" can be smaller as uploaded 2 example edited logos. We will be using this card design for many employees.
Target Market(s)
Industrial Electric Powerline, Wind Turbine, Solar Panel, & Water Utility companies.
Contact Information for Business Card
Name/Position - Dwayne Halster - Owner
Address: 4875 FM 309
Dunmore, OK 73521
Phone number - (580) 482-5096

```html
<!DOCTYPE html>
<html lang="en">
<head>
<meta charset="utf-8">
<title>Corvane Construction – Business Cards</title>
<link href="https://fonts.googleapis.com/css2?family=Marcellus&family=Roboto:wght@300;400;700&display=swap" rel="stylesheet">
<style>
  :root {
    --backdrop: #ebebeb;
    --card: #2f2f2f;
    --ink: #f4f4f4;
    --ink-soft: #cfcfcf;
    --rule: #bdbdbd;
    --mark: #7a7a7a;
  }
  * { box-sizing: border-box; margin: 0; padding: 0; }
  html, body { width: 1200px; height: 801px; overflow: hidden; }
  body {
    background: var(--backdrop);
    font-family: "Roboto", sans-serif;
    color: var(--ink);
    position: relative;
  }
  .card {
    position: absolute;
    top: 246px;
    width: 540px;
    height: 309px;
    background: var(--card);
    border-radius: 3px;
    box-shadow: 0 6px 18px rgba(0,0,0,.18);
    overflow: hidden;
  }
  .card--front { left: 45px; }
  .card--back { left: 615px; }

  /* front */
  .wordmark {
    position: absolute;
    top: 44px;
    left: 0;
    right: 0;
    text-align: center;
    font-family: "Marcellus", serif;
    color: var(--ink);
  }
  .wordmark__name { font-size: 34px; letter-spacing: 3px; line-height: 1; }
  .wordmark__sub { font-size: 22px; letter-spacing: 2px; margin-top: 6px; }
  .divider {
    position: absolute;
    left: 34px; right: 34px;
    top: 150px;
    height: 1px;
    background: var(--rule);
  }
  .person {
    position: absolute;
    left: 34px;
    top: 172px;
  }
  .person__name { font-weight: 700; font-size: 19px; }
  .person__role { font-weight: 300; font-size: 12px; color: var(--ink-soft); margin-top: 3px; }
  .person__rule { width: 150px; height: 1px; background: var(--rule); margin: 10px 0 10px; }
  .contacts { list-style: none; font-weight: 300; font-size: 13px; line-height: 20px; }
  .contacts li { display: flex; align-items: center; gap: 9px; }
  .contacts svg { width: 11px; height: 11px; flex: none; }
  .address {
    position: absolute;
    right: 34px;
    top: 176px;
    text-align: right;
    font-weight: 300;
    font-size: 13px;
    line-height: 19px;
    font-style: normal;
  }

  /* back */
  .services {
    position: absolute;
    top: 22px;
    right: 30px;
    text-align: right;
    font-weight: 300;
    font-size: 14px;
    line-height: 18px;
    list-style: none;
  }
  .services .gap { margin-top: 12px; }
  .services .lead { color: var(--ink-soft); }
  .backmark-sub {
    position: absolute;
    right: 30px;
    top: 206px;
    font-family: "Marcellus", serif;
    font-size: 24px;
    letter-spacing: 1px;
    line-height: 1;
  }
  .backmark {
    position: absolute;
    left: 22px;
    bottom: 16px;
    font-family: "Marcellus", serif;
    font-size: 54px;
    letter-spacing: 3px;
    color: var(--mark);
    line-height: 1;
  }
</style>
</head>
<body>

<section class="card card--front" aria-label="Business card front">
  <div class="wordmark">
    <div class="wordmark__name">CORVANE</div>
    <div class="wordmark__sub">CONSTRUCTION</div>
  </div>
  <div class="divider"></div>

  <div class="person">
    <div class="person__name">Dwayne Halster</div>
    <div class="person__role">Owner</div>
    <div class="person__rule"></div>
    <ul class="contacts">
      <li>
        <svg viewBox="0 0 12 12" aria-hidden="true"><path d="M2.5 1 L4.5 1 L5.2 3.6 L3.9 4.6 Q5 7 7.4 8.1 L8.4 6.8 L11 7.5 L11 9.5 Q10.5 11 9 11 Q1 10 1 2.8 Q1 1.3 2.5 1Z" fill="currentColor"/></svg>
        (580) 482-5096
      </li>
      <li>
        <svg viewBox="0 0 12 12" aria-hidden="true"><rect x="1" y="2.5" width="10" height="7" rx="1" fill="none" stroke="currentColor" stroke-width="1.2"/><path d="M1.5 3 L6 6.6 L10.5 3" fill="none" stroke="currentColor" stroke-width="1.2"/></svg>
        Dwayne@corvaneconstruction.com
      </li>
      <li>
        <svg viewBox="0 0 12 12" aria-hidden="true"><circle cx="6" cy="6" r="5" fill="currentColor"/><path d="M1 6 H11 M6 1 Q3 6 6 11 M6 1 Q9 6 6 11" fill="none" stroke="var(--card)" stroke-width=".8"/></svg>
        www.corvaneconstruction.com
      </li>
    </ul>
  </div>

  <address class="address">
    4875 FM 309<br>
    Dunmore, OK 73521
  </address>
</section>

<section class="card card--back" aria-label="Business card back">
  <ul class="services">
    <li><span class="lead">provided -</span> Roads, Substation Pads</li>
    <li>Temporary Pads, Site Pads</li>
    <li>Land Leveling</li>
    <li class="gap">Powerline Row Cleaning</li>
    <li>Land Clearing, Gates, Fencing</li>
    <li>Construction Entrances, Excavation</li>
    <li>Trenching, Underground Utilities</li>
    <li>Directional Boring, Pile Driving</li>
  </ul>
  <div class="backmark-sub">CONSTRUCTION</div>
  <div class="backmark">CORVANE</div>
</section>

</body>
</html>
```